ORLA - Óptica Médica - web design and concept

Website concept - Create and develop our website design and structure. ORLA is an optical store chain, and we are looking to establish our web and digital concept. In attachment there are several pictures about our stores and our logo.

The website structure should be user friendly. Colors should be light and the design as simple and minimalist as possible. There are different variations of the logothat can be used, check the file.

The website will include optical collections and sun collections as an online store. Also, a medical menu should be considered in order for clients to schedule optometry appointments. There should also be a menu for client assistance where the clients can read about glass maintenance in our workshop.
Updates

Low design quality

Number of Pages Required

5+ page

Font styles to use
Serif
Sans Serif

Requirements
Must have
• Must be user-friendly and minimalist.
• Please USE PICTURES FROM THE BRANDS we sell: MERUN, BOSKA, PNW, KOLE, BAMPE
Nice to have
• Nice to inspire: ZEK glasses (see website https://ch.shopzek.com/en/)
• Nice to inspire: https://merun-eyewear.com/
• Nice to ispire: https://www.pnwglobe.com/en/
Should not have
• Hysteric colors and shapes

```html
<!DOCTYPE html>
<html lang="en">
<head>
<meta charset="utf-8">
<title>ORLA Óptica Médica</title>
<link rel="stylesheet" href="https://fonts.googleapis.com/css2?family=Crimson+Text:wght@400;600;700&family=Roboto:wght@300;400;500;700&display=swap">
<style>
:root{
  --gold:#b08d57;
  --gold-dark:#9a7844;
  --ink:#222222;
  --text:#555555;
  --muted:#8a8a8a;
  --line:#e4e4e4;
  --cream:#fdf7ec;
  --footer:#1f1f1f;
  --footer-text:#bdbdbd;
  --white:#ffffff;
}
*{box-sizing:border-box;margin:0;padding:0}
html,body{width:1200px;height:5248px;overflow:hidden}
body{position:relative;background:var(--white);font-family:"Roboto",Arial,sans-serif;color:var(--text)}
.abs{position:absolute}
.serif{font-family:"Crimson Text",Georgia,serif}
.section-title{position:absolute;left:0;width:1200px;text-align:center;font-family:"Crimson Text",Georgia,serif;font-size:40px;font-weight:400;color:var(--ink);letter-spacing:1px}
.photo{position:absolute}

/* header */
.site-header{position:absolute;left:0;top:0;width:1200px;height:88px;background:var(--white)}
.brand{position:absolute;left:105px;top:22px;font-family:"Crimson Text",Georgia,serif;font-size:30px;font-weight:600;color:var(--ink);letter-spacing:3px}
.main-nav{position:absolute;left:362px;top:36px;display:flex;gap:30px;font-size:14px;font-weight:500;color:var(--ink)}
.nav-icon{position:absolute;top:34px}
.btn-trial{position:absolute;left:945px;top:26px;width:158px;height:38px;border-radius:19px;background:var(--gold);color:var(--white);font-size:14px;font-weight:500;text-align:center;line-height:38px}

/* hero */
.hero{left:0;top:88px;width:1200px;height:465px;background:linear-gradient(100deg,#eef1f3 0%,#d9dee2 45%,#9aa3a9 75%,#6d7479 100%)}
.hero-title{position:absolute;left:105px;top:222px;font-family:"Crimson Text",Georgia,serif;font-size:44px;font-weight:700;color:var(--ink);letter-spacing:1px}
.hero-sub{position:absolute;left:105px;top:292px;width:470px;font-size:18px;line-height:30px;color:var(--ink)}
.btn-gold{position:absolute;background:var(--gold);color:var(--white);text-align:center;border-radius:24px;font-weight:500}
.dots{position:absolute;display:flex;gap:8px}
.dot{width:10px;height:10px;border-radius:50%;border:1px solid var(--muted);background:transparent}
.dot.on{background:var(--muted)}

/* about */
.about-title{position:absolute;left:605px;top:648px;font-family:"Crimson Text",Georgia,serif;font-size:40px;color:var(--ink)}
.about-text{position:absolute;left:605px;top:720px;width:495px;font-size:14px;line-height:26px;color:var(--text)}

/* products */
.product-card{position:absolute;left:98px;top:1400px;width:1008px;height:320px}
.product-name{position:absolute;left:0;top:12px;font-size:22px;font-weight:700;color:var(--ink)}
.product-desc{position:absolute;left:0;top:66px;width:470px;font-size:13.5px;line-height:25px;color:var(--text)}
.stars{position:absolute;left:0;top:216px;display:flex;gap:2px}
.price{position:absolute;left:0;top:246px;font-size:16px;color:#c0392b}
.btn-cart{position:absolute;left:0;top:282px;width:104px;height:34px;background:var(--gold);color:var(--white);font-size:13px;text-align:center;line-height:34px}
.btn-buy{position:absolute;left:134px;top:282px;width:104px;height:34px;background:#eeeeee;color:var(--ink);font-size:13px;text-align:center;line-height:34px}

/* arrivals */
.arrival{position:absolute;top:1978px;width:330px;height:210px}
.arrival .photo{left:0;top:0;width:330px;height:150px;border-radius:4px}
.arrival-name{position:absolute;left:0;top:178px;width:330px;text-align:center;font-size:22px;color:var(--ink)}
.heart{position:absolute;right:8px;top:6px}
.slider-arrow{position:absolute}

/* promo */
.promo-title{position:absolute;font-size:28px;font-weight:500;color:var(--ink);text-align:center}
.promo-text{position:absolute;font-size:13.5px;line-height:25px;color:var(--text);text-align:center}
.btn-outline{position:absolute;border:1px solid var(--gold);color:var(--gold);font-size:13px;letter-spacing:1px;text-align:center;background:var(--white)}

/* guarantees */
.guarantees{left:0;top:3262px;width:1200px;height:473px;background:var(--cream)}
.guarantee{position:absolute;top:3482px;width:320px}
.guarantee-title{position:absolute;left:70px;top:0;width:250px;font-size:20px;line-height:28px;color:var(--ink)}
.guarantee-text{position:absolute;left:70px;top:70px;width:250px;font-size:14px;line-height:28px;color:var(--text)}
.guarantee svg{position:absolute;left:0;top:2px}

/* brands */
.brand-mark{position:absolute;top:3944px;width:200px;text-align:center;font-family:"Roboto",Arial,sans-serif;font-size:22px;font-weight:400;color:#777777;letter-spacing:2px}

/* blog */
.post{position:absolute;top:4288px;width:284px;height:377px;background:var(--white);box-shadow:0 4px 14px rgba(0,0,0,.18)}
.post .photo{left:0;top:0;width:284px;height:167px}
.post-excerpt{position:absolute;left:30px;top:210px;width:224px;font-size:14px;line-height:25px;color:var(--text);text-align:center}
.post-meta{position:absolute;left:0;top:320px;width:284px;text-align:center;font-size:13px;color:var(--gold)}

/* footer */
.site-footer{position:absolute;left:0;top:4778px;width:1200px;height:470px;background:var(--footer)}
.footer-head{position:absolute;top:70px;font-family:"Crimson Text",Georgia,serif;font-size:22px;color:var(--white)}
.footer-rule{position:absolute;top:104px;width:40px;height:2px;background:var(--gold)}
.footer-text{position:absolute;top:130px;font-size:13px;line-height:30px;color:var(--footer-text)}
.footer-row{display:flex;align-items:flex-start;gap:10px}
.footer-links{position:absolute;left:955px;top:130px;font-size:13px;line-height:30px;color:var(--footer-text)}
.footer-links li{list-style:none}
.copyright{position:absolute;left:0;top:436px;width:1200px;text-align:center;font-size:12px;color:var(--footer-text)}
</style>
</head>
<body>

<header class="site-header">
  <div class="brand">ORLA</div>
  <nav class="main-nav"><span>Home</span><span>About Us</span><span>Products</span><span>Contact</span><span>Blog</span><span>Store</span></nav>
  <svg class="nav-icon" style="left:822px" width="20" height="20" viewBox="0 0 20 20"><circle cx="8" cy="8" r="6" fill="none" stroke="#222" stroke-width="2"/><line x1="12.5" y1="12.5" x2="18" y2="18" stroke="#222" stroke-width="2"/></svg>
  <svg class="nav-icon" style="left:880px" width="22" height="20" viewBox="0 0 22 20"><path d="M1 2h4l3 11h11l2-8H6" fill="none" stroke="#222" stroke-width="2"/><circle cx="9" cy="17" r="1.8" fill="#222"/><circle cx="17" cy="17" r="1.8" fill="#222"/></svg>
  <div class="btn-trial">Get Free Trial</div>
</header>

<section>
  <div class="photo hero" role="img" aria-label="Smiling woman wearing glasses and a striped hat by the waterside"></div>
  <h1 class="hero-title">ORLA OPTICA MEDICA</h1>
  <p class="hero-sub">We will be happy to help you and offer you the best solution for your visual health problems.</p>
  <div class="btn-gold" style="left:105px;top:392px;width:165px;height:46px;line-height:46px;font-size:17px">Contact Us</div>
  <div class="dots" style="left:570px;top:520px"><span class="dot on"></span><span class="dot"></span><span class="dot"></span></div>
</section>

<section>
  <div class="photo" style="left:98px;top:658px;width:430px;height:567px;background:linear-gradient(180deg,#3a3530 0%,#6b5a45 45%,#c9c2b8 70%,#e6e2dc 100%)" role="img" aria-label="Interior of an optical store with display walls and a chandelier"></div>
  <h2 class="about-title">ABOUT US</h2>
  <p class="about-text">Lorem ipsum dolor sit amet, consectetur adipiscing elit, sed do eiusmod tempor incididunt ut labore et dolore magna aliqua. Ut enim ad minim veniam, quis nostrud exercitation ullamco laboris nisi ut aliquip ex ea commodo consequat. Duis aute irure dolor in reprehenderit in voluptate velit esse cillum dolore eu fugiat nulla pariatur.</p>
  <div class="btn-gold" style="left:605px;top:920px;width:137px;height:40px;line-height:40px;font-size:13px;border-radius:20px">READ MORE</div>
  <div class="photo" style="left:550px;top:1022px;width:272px;height:203px;background:linear-gradient(135deg,#f3a23c 0%,#e86a3a 45%,#6fb6d6 100%)" role="img" aria-label="Woman in a straw hat wearing mirrored sunglasses"></div>
  <div class="photo" style="left:843px;top:1022px;width:256px;height:203px;background:linear-gradient(135deg,#f4f4f4 0%,#dfe9e8 50%,#2ec9a8 100%)" role="img" aria-label="Contact lens case"></div>
</section>

<section>
  <h2 class="section-title" style="top:1314px">PRODUCTS</h2>
  <div class="product-card">
    <h3 class="product-name">SUN GLASSES</h3>
    <p class="product-desc">Protect yourself adequately from ultraviolet (UV) rays thanks to our wide range of glasses, photochromic lenses and polarized lenses. Dress your look with the best quality and with prestigious brands: Stellan Berg, Northmoor, Halden, Lumen, Corvetta...</p>
    <div class="stars">
      <svg width="70" height="12" viewBox="0 0 70 12"><g fill="#c0392b"><path id="st" d="M6 0l1.8 4 4.2.4-3.2 2.8 1 4.2L6 9.2 2.2 11.4l1-4.2L0 4.4 4.2 4z"/><use href="#st" x="14"/><use href="#st" x="28"/><use href="#st" x="42"/><use href="#st" x="56"/></g></svg>
    </div>
    <div class="price">£349.00</div>
    <div class="btn-cart">Add To Cart</div>
    <div class="btn-buy">Buy Now</div>
    <div class="photo" style="left:522px;top:0;width:486px;height:320px;box-shadow:0 2px 10px rgba(0,0,0,.15);background:linear-gradient(160deg,#d8c9b6 0%,#bfae98 50%,#a8977f 100%)" role="img" aria-label="Mirrored sunglasses lying on sand"></div>
  </div>
  <div class="dots" style="left:580px;top:1770px"><span class="dot on"></span><span class="dot"></span><span class="dot"></span></div>
</section>

<section>
  <h2 class="section-title" style="top:1870px">NEW ARRIVALS</h2>
  <svg class="slider-arrow" style="left:40px;top:2045px" width="16" height="26" viewBox="0 0 16 26"><path d="M13 2L3 13l10 11" fill="none" stroke="#999" stroke-width="3"/></svg>
  <svg class="slider-arrow" style="left:1142px;top:2045px" width="16" height="26" viewBox="0 0 16 26"><path d="M3 2l10 11L3 24" fill="none" stroke="#999" stroke-width="3"/></svg>
  <div class="arrival" style="left:70px"><div class="photo" style="background:radial-gradient(ellipse at center,#6b5246 0%,#2b2420 35%,#ffffff 62%)" role="img" aria-label="Dark sunglasses"></div><svg class="heart" width="20" height="18" viewBox="0 0 20 18"><path d="M10 16S2 11 2 6a4 4 0 0 1 8-1 4 4 0 0 1 8 1c0 5-8 10-8 10z" fill="none" stroke="#333" stroke-width="1.6"/></svg><div class="arrival-name">PERSPICIATIS</div></div>
  <div class="arrival" style="left:435px"><div class="photo" style="background:radial-gradient(ellipse at center,#5a4038 0%,#221b18 35%,#ffffff 62%)" role="img" aria-label="Tortoiseshell sunglasses"></div><svg class="heart" width="20" height="18" viewBox="0 0 20 18"><path d="M10 16S2 11 2 6a4 4 0 0 1 8-1 4 4 0 0 1 8 1c0 5-8 10-8 10z" fill="none" stroke="#333" stroke-width="1.6"/></svg><div class="arrival-name">PERSPICIATIS</div></div>
  <div class="arrival" style="left:790px"><div class="photo" style="background:radial-gradient(ellipse at center,#7a5a40 0%,#2e241d 35%,#ffffff 62%)" role="img" aria-label="Brown sunglasses"></div><svg class="heart" width="20" height="18" viewBox="0 0 20 18"><path d="M10 16S2 11 2 6a4 4 0 0 1 8-1 4 4 0 0 1 8 1c0 5-8 10-8 10z" fill="none" stroke="#333" stroke-width="1.6"/></svg><div class="arrival-name">PERSPICIATIS</div></div>
</section>

<section>
  <div class="photo" style="left:0;top:2282px;width:602px;height:490px;background:linear-gradient(120deg,#d9c2a6 0%,#b99375 45%,#6f8da0 100%)" role="img" aria-label="Couple laughing together wearing sunglasses"></div>
  <h3 class="promo-title" style="left:640px;top:2402px;width:520px">Man and Women Glasses</h3>
  <p class="promo-text" style="left:670px;top:2466px;width:460px">Sed ut perspiciatis unde omnis iste natus error sit voluptatem accusantium doloremque laudantium, totam rem aperiam, eaque ipsa quae ab illo inventore veritatis et quasi architecto.</p>
  <div class="btn-outline" style="left:837px;top:2604px;width:126px;height:42px;line-height:40px">SHOP NOW</div>

  <h3 class="promo-title" style="left:40px;top:2892px;width:520px">Collection of sunglasses</h3>
  <p class="promo-text" style="left:70px;top:2956px;width:460px">Sed ut perspiciatis unde omnis iste natus error sit voluptatem accusantium doloremque laudantium, totam rem aperiam, eaque ipsa quae ab illo inventore veritatis et quasi architecto.</p>
  <div class="btn-outline" style="left:252px;top:3094px;width:126px;height:42px;line-height:40px">SHOP NOW</div>
  <div class="photo" style="left:602px;top:2772px;width:598px;height:490px;background:linear-gradient(150deg,#7fae6a 0%,#a9c48a 40%,#c9b48f 70%,#6d8a4c 100%)" role="img" aria-label="Woman in sunglasses sitting in a sunny garden"></div>
</section>

<section>
  <div class="abs guarantees"></div>
  <h2 class="section-title" style="top:3358px">OUR GUARANTEES</h2>
  <svg class="slider-arrow" style="left:38px;top:3488px" width="14" height="22" viewBox="0 0 14 22"><path d="M11 2L3 11l8 9" fill="none" stroke="#111" stroke-width="3"/></svg>
  <svg class="slider-arrow" style="left:1146px;top:3488px" width="14" height="22" viewBox="0 0 14 22"><path d="M3 2l8 9-8 9" fill="none" stroke="#111" stroke-width="3"/></svg>
  <div class="guarantee" style="left:105px">
    <svg width="34" height="40" viewBox="0 0 34 40"><g fill="none" stroke="#b08d57" stroke-width="2"><circle cx="17" cy="8" r="6"/><path d="M8 38V24l-5-6M26 38V24l5-6M8 20h18v10H8z"/></g></svg>
    <div class="guarantee-title">Orla Childhood Guarantee</div>
    <div class="guarantee-text">50% discount on new glasses, if your child's graduation has changed before six months.</div>
  </div>
  <div class="guarantee" style="left:448px">
    <svg width="40" height="30" viewBox="0 0 40 30"><g fill="none" stroke="#b08d57" stroke-width="2"><path d="M3 20v-6l5-8h20l6 8h3v6z"/><circle cx="11" cy="22" r="3.5"/><circle cx="29" cy="22" r="3.5"/></g></svg>
    <div class="guarantee-title">Orla Accident Warranty</div>
    <div class="guarantee-text">Did you get off your glasses when you got out of the car? Did your little boy play with his sunglasses?</div>
  </div>
  <div class="guarantee" style="left:815px">
    <svg width="36" height="38" viewBox="0 0 36 38"><g fill="none" stroke="#b08d57" stroke-width="2"><circle cx="18" cy="9" r="6"/><path d="M5 36c0-9 6-14 13-14s13 5 13 14"/><rect x="12" y="26" width="12" height="8"/></g></svg>
    <div class="guarantee-title">Orla Security</div>
    <div class="guarantee-text">If you have suffered a robbery or robbery in your home, you will opt for the replacement of the same product at half price.</div>
  </div>
</section>

<section>
  <h2 class="section-title" style="top:3826px">OUR BRANDS</h2>
  <div class="brand-mark" style="left:57px">Rosa Marín</div>
  <div class="brand-mark" style="left:285px">Vellano</div>
  <div class="brand-mark" style="left:502px">Jiro Kade</div>
  <div class="brand-mark" style="left:715px">Halden</div>
  <div class="brand-mark" style="left:932px">Corvetta</div>
</section>

<section>
  <h2 class="section-title" style="top:4094px">LATEST BLOG</h2>
  <article class="post" style="left:98px"><div class="photo" style="background:linear-gradient(120deg,#5b7a8a 0%,#b7c4cb 50%,#f1e9e0 100%)" role="img" aria-label="Optometrist with an article banner about eyelid care"></div><p class="post-excerpt">Lorem ipsum dolor sit amet, consectetur adipiscing elit, sed do eiusmod tempor incididunt</p><div class="post-meta">&#9675; 10 &nbsp; &#9675; March 3,2017</div></article>
  <article class="post" style="left:460px"><div class="photo" style="background:linear-gradient(120deg,#7a3fa8 0%,#d94c8c 50%,#f3c74a 100%)" role="img" aria-label="Opinion article banner about sunglasses for children"></div><p class="post-excerpt">Lorem ipsum dolor sit amet, consectetur adipiscing elit, sed do eiusmod tempor incididunt</p><div class="post-meta">&#9675; 10 &nbsp; &#9675; March 3,2017</div></article>
  <article class="post" style="left:822px"><div class="photo" style="background:linear-gradient(120deg,#1f6fa8 0%,#6fb5d8 45%,#f0d24c 100%)" role="img" aria-label="Article banner about sun protection for the eyes"></div><p class="post-excerpt">Lorem ipsum dolor sit amet, consectetur adipiscing elit, sed do eiusmod tempor incididunt</p><div class="post-meta">&#9675; 10 &nbsp; &#9675; March 3,2017</div></article>
</section>

<footer class="site-footer">
  <h4 class="footer-head" style="left:98px">Who We Are</h4><div class="footer-rule" style="left:98px"></div>
  <p class="footer-text" style="left:98px;width:250px">ORLA OPTICA opens its doors with a clear purpose: to take care of you. Our priority is your visual health and for this reason we have the best professionals and the most competitive products to serve your needs.</p>
  <div class="btn-gold" style="left:98px;top:360px;width:206px;height:42px;line-height:42px;font-size:12px;border-radius:21px">BOOK AN APPOINTMENT</div>

  <h4 class="footer-head" style="left:388px">Contact Details</h4><div class="footer-rule" style="left:388px"></div>
  <div class="footer-text" style="left:388px;width:260px">
    <div class="footer-row"><svg width="14" height="18" viewBox="0 0 14 18" style="margin-top:7px"><path d="M7 17S1 10 1 6.5a6 6 0 0 1 12 0C13 10 7 17 7 17z" fill="none" stroke="#b08d57" stroke-width="1.6"/><circle cx="7" cy="6.5" r="2" fill="#b08d57"/></svg><span>Calle del Roble, 22, Soria</span></div>
    <div class="footer-row"><svg width="14" height="14" viewBox="0 0 14 14" style="margin-top:8px"><path d="M3 1l2.5 3-1.5 1.5a8 8 0 0 0 4.5 4.5L10 8.5l3 2.5-1.5 2C6 13 1 8 1 2.5z" fill="#b08d57"/></svg><span>Telephone 900 555 218</span></div>
    <div class="footer-row"><svg width="14" height="12" viewBox="0 0 14 12" style="margin-top:9px"><rect x="1" y="1" width="12" height="10" fill="none" stroke="#b08d57" stroke-width="1.4"/><path d="M1 1l6 5 6-5" fill="none" stroke="#b08d57" stroke-width="1.4"/></svg><span>hola@orlaoptica.test</span></div>
  </div>

  <h4 class="footer-head" style="left:682px">Opening Hours</h4><div class="footer-rule" style="left:682px"></div>
  <div class="footer-text" style="left:682px;width:240px">
    <div class="footer-row"><svg width="14" height="14" viewBox="0 0 14 14" style="margin-top:8px"><circle cx="7" cy="7" r="6" fill="none" stroke="#b08d57" stroke-width="1.4"/><path d="M7 3v4h3" fill="none" stroke="#b08d57" stroke-width="1.4"/></svg><span>Monday - Friday: 10:00 - 14:00 &amp;<br>17:00 - 20:30<br>Saturday: 10:00 - 14:00</span></div>
  </div>

  <h4 class="footer-head" style="left:955px">Quick Links</h4><div class="footer-rule" style="left:955px"></div>
  <ul class="footer-links"><li>&rsaquo;&nbsp; Home</li><li>&rsaquo;&nbsp; About Us</li><li>&rsaquo;&nbsp; Products</li><li>&rsaquo;&nbsp; Contact</li><li>&rsaquo;&nbsp; Blog</li><li>&rsaquo;&nbsp; Store</li></ul>

  <p class="copyright">&copy; Copyrights 2018 Orlaoptica All Rights Reserved</p>
</footer>

</body>
</html>
```